KRT Info Brochure

We need a brochure design for a new not-for-profit organisation that is aimed at providing homeless people with a residence that also provides counselling and vocational training to assist them to find suitable employment at the end of the program.
PLEASE NOTE:
Brochure to be A4.
I know the brochure is quite long, it is really a booklet, but please note that it does not have to have a lot of work done on it, I just want it to look professional and the front cover and inside page to look good.
Also please leave about 2-3 pages at the end as I will be adding in some architect drawings.
Please add in a last page with Contact written at the bottom - we will fill that in later. So please ensure it is editable in PDF.
Thank you so much.
Cheers
Marta

```html
<!DOCTYPE html>
<html lang="en">
<head>
<meta charset="utf-8">
<title>KRT Info Brochure – Complimentary Businesses</title>
<link href="https://fonts.googleapis.com/css2?family=Arimo:wght@400;700&display=swap" rel="stylesheet">
<style>
  :root {
    --backdrop: #ececec;
    --paper: #ffffff;
    --olive: #8d8a38;
    --olive-dark: #6f6c26;
    --olive-light: #b3b063;
    --gold: #f0b323;
    --orange: #eba51d;
    --ink: #2b2b2b;
  }
  * { box-sizing: border-box; margin: 0; padding: 0; }
  html, body { width: 1200px; height: 847px; overflow: hidden; }
  body {
    background: radial-gradient(ellipse at 50% 40%, #f7f7f7, var(--backdrop));
    font-family: "Arimo", Arial, sans-serif;
    color: var(--ink);
  }
  .spread {
    position: absolute; left: 50px; top: 60px;
    width: 1100px; height: 727px;
    display: flex;
    box-shadow: 0 12px 30px rgba(0,0,0,.18);
  }
  .page { position: relative; width: 550px; height: 727px; background: var(--paper); overflow: hidden; }
  .page-left { box-shadow: inset -14px 0 18px -14px rgba(0,0,0,.25); }
  .page-right { box-shadow: inset 14px 0 18px -14px rgba(0,0,0,.25); }
  .page-art { position: absolute; inset: 0; width: 550px; height: 727px; }
  .block { position: absolute; }
  .section-title { font-size: 18px; font-weight: 700; color: var(--olive); }
  .phase-title { font-size: 15px; font-weight: 700; color: var(--olive); line-height: 17px; }
  .sub-title { font-size: 12px; font-weight: 700; color: var(--orange); line-height: 15px; }
  p { font-size: 9.5px; line-height: 12px; }
  p + p { margin-top: 7px; }
  .photo {
    position: absolute;
    border: 5px solid var(--olive-dark);
    box-shadow: 0 2px 4px rgba(0,0,0,.2);
  }
  .photo-coffee { background: linear-gradient(135deg, #d9d4cc, #6b5a4a 60%, #2a2420); }
  .photo-orchard { background: linear-gradient(160deg, #5f7a2a, #3d5a1e 60%, #8a7a40); }
  .photo-venue { background: linear-gradient(170deg, #5a3e2a, #c9b69a 55%, #efe6d6); }
  .photo-florist { background: linear-gradient(120deg, #f2f0ea, #d45a7a 55%, #e8c740); }
  .photo-camera { background: linear-gradient(140deg, #d9c48a, #8aa04a 60%, #3a3a36); }
</style>
</head>
<body>
<div class="spread">

  <section class="page page-left">
    <svg class="page-art" viewBox="0 0 550 727" aria-hidden="true">
      <defs>
        <linearGradient id="oliveBand" x1="0" y1="0" x2="1" y2="1">
          <stop offset="0" stop-color="#a3a04c"/>
          <stop offset="1" stop-color="#6f6c26"/>
        </linearGradient>
      </defs>
      <path d="M0 0 H550 V38 C420 48 200 62 0 76 Z" fill="url(#oliveBand)"/>
      <path d="M0 82 C200 68 420 54 550 44" stroke="var(--gold)" stroke-width="3" fill="none"/>
      <path d="M0 655 C180 668 380 664 550 640 V727 H0 Z" fill="url(#oliveBand)"/>
      <path d="M0 648 C180 660 380 656 550 632" stroke="var(--gold)" stroke-width="3" fill="none"/>
    </svg>

    <div class="block" style="left:30px; top:92px; width:495px;">
      <h1 class="section-title">5.1.Complimentary Businesses</h1>
      <p style="margin-top:6px;">The complimentary business will be introduced in five phases within the first five years. The aim is to establish as much of the infrastructure framework as possible initially and then as finances and resources become available, complimentary businesses will be established. Each complimentary business will build upon the one before with the aim of the complimentary businesses being suppliers to the other businesses. It is also envisaged that some of the KRT complimentary businesses will become tourist attractions in the Hillview Coast hinterland tourist belt.</p>
      <p>These businesses will provide the requisite experience work experience for Residents to assist them in the employments skills aspect of their program. Additionally, these businesses will also provide some Residents with employment upon completion of their training (for example the KRT Greys will be established to provide the over 55's category with part time employment).</p>
    </div>

    <div class="block" style="left:30px; top:245px; width:265px;">
      <h2 class="phase-title">5.1.1. Phase 1</h2>
      <h3 class="sub-title">a) Coffee shop and gallery</h3>
      <p>The first business to be established will be the KRT coffee shop and gallery. The coffee shop and gallery will be open to the public. Through the KRT program, Residents will undertake various types of therapeutic classes, such as woodwork, painting, photography, knitting, soap-making etc, they will be able to put their best work in the gallery on consignment, funds from sales will be added to the Residents bank accounts, which will assist them to become independent. The Coffee shop will serve healthy options grown at the KRT complex farm, grown by KRT Residents. The coffee shop will be open for breakfast and lunch on weekends and during the week as the business becomes more established.</p>
      <h3 class="sub-title" style="margin-top:10px;">b) Organic Farm and Orchard</h3>
      <p>The KRT Farm will provide fruit, vegetables, eggs and flowers for all other complimentary business. The fruit and vegetables will be grown organically. KRT Residents studying farming and horticulture will gain invaluable experience. The farm will be established in the initial phase of development, to take advantage of the excavation equipment that will be available at the initial build and to give the fruit and vegetables time to mature. In addition, a recycling chicken run will be built for eggs. The chicken coop will be built to recycle chicken waste and allow the chickens to 'work' the composite for the fruit and vegetables.</p>
    </div>

    <div class="photo photo-coffee" role="img" aria-label="Photo of coffee being poured into a cup at a café counter" style="left:308px; top:248px; width:215px; height:140px;"></div>
    <div class="photo photo-orchard" role="img" aria-label="Photo of a resident holding a basket of freshly picked apples in an orchard" style="left:308px; top:425px; width:215px; height:150px;"></div>
  </section>

  <section class="page page-right">
    <svg class="page-art" viewBox="0 0 550 727" aria-hidden="true">
      <defs>
        <linearGradient id="oliveBandR" x1="0" y1="0" x2="1" y2="1">
          <stop offset="0" stop-color="#a3a04c"/>
          <stop offset="1" stop-color="#6f6c26"/>
        </linearGradient>
        <pattern id="stripes" width="10" height="10" patternUnits="userSpaceOnUse">
          <rect width="10" height="10" fill="#a9a656"/>
          <rect width="5" height="10" fill="#c9c78a"/>
        </pattern>
      </defs>
      <path d="M0 0 H550 V36 C420 48 200 58 0 74 Z" fill="url(#oliveBandR)"/>
      <path d="M0 0 H110 V66 C70 69 35 72 0 74 Z" fill="url(#stripes)"/>
      <path d="M0 80 C200 64 420 54 550 42" stroke="var(--gold)" stroke-width="3" fill="none"/>
      <path d="M0 640 C180 664 380 668 550 655 V727 H0 Z" fill="url(#oliveBandR)"/>
      <path d="M0 646 C40 651 75 655 110 657 V727 H0 Z" fill="url(#stripes)"/>
      <path d="M0 632 C180 656 380 660 550 648" stroke="var(--gold)" stroke-width="3" fill="none"/>
    </svg>

    <div class="block" style="left:30px; top:86px; width:262px;">
      <h2 class="phase-title">5.1.2. Phase 2</h2>
      <h3 class="sub-title">a) Wedding/Events Venue</h3>
      <p>The wedding venue will offer reduced prices for weddings in order to allow KRT Residents to obtain valuable experience in vocational fields of study, such as hospitality (cooking, waiting, bar staff, kitchen hand), photography, floristry and event management. In addition the Hillview Coast hinterland is an ideal location for weddings and meetings and is estimated to return a profit of over $70,000 per month. It is further envisaged that the other complimentary businesses will act as suppliers to the wedding venue, reducing overall costs and increasing profitability.</p>
    </div>

    <div class="photo photo-venue" role="img" aria-label="Photo of a decorated wedding reception hall with dressed tables and chandeliers" style="left:298px; top:52px; width:225px; height:165px;"></div>

    <div class="photo photo-florist" role="img" aria-label="Photo of a florist holding a bouquet among colourful flowers" style="left:30px; top:262px; width:250px; height:160px;"></div>

    <div class="block" style="left:300px; top:238px; width:225px;">
      <h2 class="phase-title">5.1.3.Phase 3</h2>
      <h3 class="sub-title">a) KRT Florist</h3>
      <p>KRT Florists will provide valuable vocational experience to Residents and will be a complimentary business to the wedding venue and attached to the Coffee Shop. The flowers will be grown at the KRT complex, so costs will be kept at a minimum. Residents will be taught by an experienced florist and may gain work experience with locally located florists with the aim of placing residents in paid work upon becoming independent.</p>
    </div>

    <div class="photo photo-camera" role="img" aria-label="Photo of a photographer holding a camera outdoors" style="left:305px; top:420px; width:218px; height:140px;"></div>

    <div class="block" style="left:30px; top:440px; width:262px;">
      <h3 class="sub-title">b) KRT Photography</h3>
      <p>Again the photography business will be complimentary to the wedding venue. Again Residents will be taught by an experienced professional and can gain valuable experience at weddings held at the venue. In addition, Residents can display their work for sale at the Coffee Shop Gallery and online on consignment. As previously mentioned, any sales will be deposited to the individual Residents bank account, to assist them with independent living.</p>
    </div>
  </section>

</div>
</body>
</html>
```